Website for a service provided by a Canadian Immigration Company

Design and Code a website for a Canadian immigration company which provides service to clients all across the world. the website should be very Canadian centric and have 4-5 pages. Basic, classy modern. I have the logo s already designed. Please contact me and I can send you some more details. It's basically a service which is provided to clients who are below 17 and need a guardian in canada to sign their documents that they will be looked after them. It's called custodianship. You can google the term and you will understand what it means
Updates

didn't realize it was just a day

Target Market(s)

17-55

Industry/Entity Type

Immigration

Coding

Coded - Design and coding required

Number of Pages Required

5+ page

Font styles to use
Sans Serif

Colors
EE7325
F08F49
F5BC92
FAE3D3
FDF4ED
EB3D1F
EC4F4E
F09395
F8D3D4
FCEDEE

Requirements
Must have
• Pages with some graphics, some small animations like clients served, projects completed

```html
<!DOCTYPE html>
<html lang="en">
<head>
<meta charset="utf-8">
<title>Ward Maple — Canadian Immigration Company</title>
<link href="https://fonts.googleapis.com/css2?family=Mulish:wght@400;600;700;800&family=Roboto:wght@400;500;700&display=swap" rel="stylesheet">
<style>
:root{
  --red:#ec1c24;
  --red-dark:#c4161d;
  --ink:#2b2b2b;
  --text:#6a6a6a;
  --peach-top:#fdebd3;
  --peach-bottom:#fbd7a9;
  --field:#e8e8e8;
  --black:#000;
  --white:#fff;
}
*{margin:0;padding:0;box-sizing:border-box}
html,body{width:1200px;height:3305px;overflow:hidden}
body{position:relative;background:var(--white);font-family:"Mulish",sans-serif;color:var(--ink)}
.abs{position:absolute}
.btn{position:absolute;background:var(--red);color:var(--white);font-weight:700;font-size:15px;display:flex;align-items:center;justify-content:center;gap:6px;text-decoration:none}

/* header */
.site-header{position:absolute;left:0;top:0;width:1200px;height:68px;background:var(--white);z-index:3}
.brand{position:absolute;left:112px;top:18px;display:flex;align-items:center;gap:10px;font-size:22px;font-weight:700;color:var(--ink)}
.brand-mark{width:30px;height:30px;background:var(--red)}
.main-nav{position:absolute;left:544px;top:0;height:68px;display:flex;gap:38px;font-size:15.5px}
.main-nav a{color:var(--ink);text-decoration:none;line-height:66px;position:relative}
.main-nav a.active{color:var(--red)}
.main-nav a.active::after{content:"";position:absolute;left:0;right:0;bottom:0;height:3px;background:var(--red)}
.quote-btn{left:961px;top:15px;width:128px;height:38px;font-size:15.5px}

/* hero */
.hero-photo{left:0;top:68px;width:1200px;height:721px;
  background:linear-gradient(160deg,#5b6672 0%,#a89a92 35%,#8a7e83 60%,#5d6f92 100%);
  clip-path:polygon(0 0,100% 0,100% 569px,50% 692px,0 569px)}
.hero-title{left:0;width:1200px;top:293px;text-align:center;color:var(--white);font-size:68px;font-weight:800;text-shadow:0 2px 6px rgba(0,0,0,.3)}
.hero-sub{left:0;width:1200px;top:385px;text-align:center;color:var(--white);font-size:33px;font-weight:800;text-shadow:0 2px 6px rgba(0,0,0,.3)}
.hero-btn{left:536px;top:456px;width:128px;height:37px}
.scroll-mouse{left:588px;top:686px;width:24px;height:44px;border:2px solid var(--white);border-radius:12px}
.scroll-mouse::after{content:"";position:absolute;left:9px;top:7px;width:2px;height:9px;background:var(--white)}

/* about */
.about-photo{left:150px;top:889px;width:410px;height:455px;
  background:linear-gradient(150deg,#c8b8a8,#9aa7b4 50%,#8c6f66);
  clip-path:polygon(50% 0,100% 27%,100% 73%,50% 100%,0 73%,0 27%)}
.about-copy{left:599px;top:882px;width:489px}
.section-title{font-size:44px;font-weight:800;color:var(--ink)}
.body-text{font-size:14.5px;line-height:25.7px;color:var(--text);text-align:justify}
.about-copy .body-text{margin-top:14px}
.about-copy .body-text + .body-text{margin-top:25px}
.about-btn{left:599px;top:1303px;width:129px;height:38px}

/* what we do */
.city-photo{left:0;top:1950px;width:1200px;height:390px;
  background:linear-gradient(180deg,#f2b46a 0%,#8d8c90 20%,#51627a 55%,#2b5778 100%);
  clip-path:polygon(0 0,100% 0,100% 231px,50% 368px,0 231px)}
.wwd-title{left:0;width:1200px;top:1580px;text-align:center}
.wwd-copy{left:221px;top:1645px;width:757px}
.wwd-copy .body-text{text-align-last:center}
.wwd-copy .body-text + .body-text{margin-top:25.7px}
.wwd-btn{left:536px;top:1900px;width:128px;height:38px}

/* contact */
.contact-title{left:0;width:1200px;top:2418px;text-align:center;font-size:62px}
.field{position:absolute;background:var(--field);border:1px solid #dcdcdc;color:#7a7a7a;font-size:13px;padding:17px 20px}
.submit-btn{left:536px;top:2700px;width:128px;height:38px;font-size:14px;font-weight:700}

/* footer */
.footer-brand{left:0;width:1200px;top:2918px;display:flex;justify-content:center;align-items:center;gap:12px;color:var(--white);font-size:32px;font-weight:600}
.footer-brand .brand-mark{width:36px;height:36px;background:var(--white)}
.footer-nav{left:0;width:1200px;top:2997px;display:flex;justify-content:center;gap:30px;font-family:"Roboto",sans-serif;font-weight:700;font-size:15px;color:var(--white)}
.footer-nav span.sep{font-weight:400}
.rule{left:0;width:1200px;height:1px;background:#333}
.contact-item{position:absolute;display:flex;align-items:center;gap:16px;font-family:"Roboto",sans-serif;color:var(--white)}
.icon-ring{width:62px;height:62px;border:2px solid var(--red);border-radius:50%;display:flex;align-items:center;justify-content:center}
.contact-item strong{display:block;font-size:15px;font-weight:700;margin-bottom:6px}
.contact-item p{font-size:14px;line-height:19px}
.copyright{left:0;width:1200px;top:3192px;text-align:center;font-family:"Roboto",sans-serif;font-size:14.5px;color:var(--white)}
.social{left:530px;top:3233px;display:flex;gap:8px}
.social span{width:29px;height:29px;border:2px solid var(--white);border-radius:50%}
.chat-btn{left:1088px;top:2918px;width:75px;height:75px;border-radius:50%;background:var(--white);box-shadow:0 4px 14px rgba(0,0,0,.25)}
</style>
</head>
<body>

<header class="site-header">
  <div class="brand"><span class="brand-mark"></span>wardmaple.ca</div>
  <nav class="main-nav">
    <a class="active" href="#">Home</a>
    <a href="#">About Us</a>
    <a href="#">Services</a>
    <a href="#">Contact Us</a>
  </nav>
  <a class="btn quote-btn" href="#">Get A Quote</a>
</header>

<!-- hero -->
<div class="abs hero-photo" role="img" aria-label="Group of smiling teenage students with backpacks walking along a school corridor"></div>
<svg class="abs" style="left:0;top:0" width="1200" height="800" aria-hidden="true">
  <polygon points="0,637 600,760 1200,637 1200,660 600,789 0,660" fill="#ec1c24"/>
</svg>
<h1 class="abs hero-title">Ward Maple</h1>
<p class="abs hero-sub">Canadian Immigration Company</p>
<a class="btn hero-btn" href="#">Get Started</a>
<div class="abs scroll-mouse"></div>

<!-- about -->
<svg class="abs" style="left:0;top:860px" width="600" height="520" aria-hidden="true">
  <defs>
    <linearGradient id="hexEdge" x1="0" y1="0" x2="1" y2="1">
      <stop offset="0" stop-color="#2a0204"/>
      <stop offset="1" stop-color="#d81c24"/>
    </linearGradient>
  </defs>
  <polygon points="355,16 574,136 574,376 355,496 137,376 137,136" fill="url(#hexEdge)"/>
  <polygon points="355,30 560,144 560,368 355,482 151,368 151,144" fill="#fff"/>
</svg>
<div class="abs about-photo" role="img" aria-label="Three smiling young schoolchildren holding books in a classroom"></div>
<div class="abs about-copy">
  <h2 class="section-title">About Us</h2>
  <p class="body-text">Lorem ipsum dolor sit amet, consectetur adipiscing elit, sed do eiusmod tempor incididunt ut labore et dolore magna aliqua. Ut enim ad minim veniam, quis nostrud exercitation ullamco laboris nisi ut aliquip ex ea commodo consequat. Duis aute irure dolor in reprehenderit in voluptate velit esse cillum dolore eu fugiat nulla pariatur.</p>
  <p class="body-text">Excepteur sint occaecat cupidatat non proident, sunt in culpa qui officia deserunt mollit anim id est laborum. Lorem ipsum dolor sit amet, consectetur adipiscing elit, sed do eiusmod tempor incididunt ut labore et dolore magna aliqua. Ut enim ad minim veniam, quis nostrud exercitation ullamco laboris nisi ut aliquip ex ea commodo consequat. Duis aute irure dolor in reprehenderit in voluptate velit esse cillum dolore eu fugiat nulla pariatur.</p>
</div>
<a class="btn about-btn" href="#">Learn More <svg width="14" height="14" viewBox="0 0 14 14"><circle cx="7" cy="7" r="7" fill="#fff"/><path d="M5.5 3.8 8.7 7 5.5 10.2" stroke="#ec1c24" stroke-width="2" fill="none"/></svg></a>

<!-- what we do -->
<svg class="abs" style="left:0;top:0" width="1200" height="2000" aria-hidden="true">
  <defs>
    <linearGradient id="peach" x1="0" y1="0" x2="0" y2="1">
      <stop offset="0" stop-color="#fdebd3"/>
      <stop offset="1" stop-color="#fbd3a3"/>
    </linearGradient>
  </defs>
  <polygon points="0,1600 600,1461 1200,1600 1200,1960 0,1960" fill="url(#peach)"/>
  <polygon points="0,1580 600,1443 1200,1580 1200,1600 600,1461 0,1600" fill="#ec1c24"/>
</svg>
<div class="abs city-photo" role="img" aria-label="Aerial view of a Canadian coastal city skyline with mountains at sunset"></div>
<svg class="abs" style="left:0;top:2170px" width="1200" height="180" aria-hidden="true">
  <polygon points="0,11 600,148 1200,11 1200,36 600,166 0,36" fill="#ec1c24"/>
</svg>
<h2 class="abs section-title wwd-title">What We Do</h2>
<div class="abs wwd-copy">
  <p class="body-text">We provide the required signed and notarized custodian declaration along with formal supervision service upon the student's arrival in Canada. According to Citizenship and Immigration Canada (IRCC), minor students can be accepted at a university or college, but they cannot obtain a study permit without the required signed and notarized custodianship form.</p>
  <p class="body-text">We provide support for minor international students in Canada and peace of mind for their parents. Our warm and kindhearted Legal Custodian will guide international students through their first challenging months in a new environment. We communicate with parents to discuss their children's emotional and academic needs to ensure they achieve success, academically and personally in Canada.</p>
</div>
<a class="btn wwd-btn" href="#">Learn More <svg width="14" height="14" viewBox="0 0 14 14"><circle cx="7" cy="7" r="7" fill="#fff"/><path d="M5.5 3.8 8.7 7 5.5 10.2" stroke="#ec1c24" stroke-width="2" fill="none"/></svg></a>

<!-- contact -->
<h2 class="abs section-title contact-title">Contact Us</h2>
<div class="field" style="left:223px;top:2503px;width:245px;height:54px">First Name*</div>
<div class="field" style="left:478px;top:2503px;width:245px;height:54px">Last Name*</div>
<div class="field" style="left:733px;top:2503px;width:245px;height:54px">Company*</div>
<div class="field" style="left:223px;top:2570px;width:755px;height:110px">Message*</div>
<a class="btn submit-btn" href="#">SUBMIT NOW</a>

<!-- footer -->
<svg class="abs" style="left:0;top:2820px" width="1200" height="485" aria-hidden="true">
  <polygon points="0,142 600,6 1200,142 1200,165 600,28 0,165" fill="#ec1c24"/>
  <polygon points="0,165 600,28 1200,165 1200,485 0,485" fill="#000"/>
</svg>
<div class="abs footer-brand"><span class="brand-mark"></span>wardmaple.ca</div>
<nav class="abs footer-nav">
  <span>HOME</span><span class="sep">/</span><span>SERVICES</span><span class="sep">/</span><span>ABOUT</span><span class="sep">/</span><span>INQUIRIES</span><span class="sep">/</span><span>CONTACT</span>
</nav>
<div class="abs rule" style="top:3042px"></div>
<div class="contact-item" style="left:116px;top:3065px">
  <span class="icon-ring"><svg width="20" height="20" viewBox="0 0 24 24"><path d="M6.6 10.8a15.1 15.1 0 0 0 6.6 6.6l2.2-2.2a1 1 0 0 1 1-.25 11.4 11.4 0 0 0 3.6.57 1 1 0 0 1 1 1V20a1 1 0 0 1-1 1A17 17 0 0 1 3 4a1 1 0 0 1 1-1h3.5a1 1 0 0 1 1 1c0 1.25.2 2.45.57 3.57a1 1 0 0 1-.25 1z" fill="#ec1c24"/></svg></span>
  <div><strong>PHONE</strong><p>+1 888 888 8888</p></div>
</div>
<div class="contact-item" style="left:448px;top:3065px">
  <span class="icon-ring"><svg width="18" height="22" viewBox="0 0 18 24"><path d="M9 0a9 9 0 0 0-9 9c0 6.8 9 15 9 15s9-8.2 9-15a9 9 0 0 0-9-9zm0 12.2A3.2 3.2 0 1 1 9 5.8a3.2 3.2 0 0 1 0 6.4z" fill="#ec1c24"/></svg></span>
  <div><strong>ADDRESS</strong><p>Lorem ipsum dolor sit<br>amet dolor</p></div>
</div>
<div class="contact-item" style="left:812px;top:3065px">
  <span class="icon-ring"><svg width="24" height="18" viewBox="0 0 24 18"><rect width="24" height="18" rx="2" fill="#ec1c24"/><path d="M1 2l11 8 11-8" stroke="#000" stroke-width="2" fill="none"/></svg></span>
  <div><strong>EMAIL</strong><p>info@companyname.com</p></div>
</div>
<div class="abs rule" style="top:3155px"></div>
<p class="abs copyright">2023 Copyright - <strong style="font-weight:500">Company Name</strong> &nbsp;| All Rights Reserved</p>
<div class="abs social"><span></span><span></span><span></span><span></span></div>
<div class="abs chat-btn"></div>

</body>
</html>
```